Keel Brook Services Site Redesign

SIte redesign for a commercial/residential cleaning and restoration company.

Design style should be as for a professional service company. Use this as a guide: https://marlo.quintaweb-example.com/electrician/

Please use current site content located here: http://kbsgrv-example.com/

Design should be responsive

Site Design should include two (2) pages:
- Homepage
- Interior page (for services) with a layout that can be duplicated across the different interior pages

Please Use the following items for the Navigation:
• Water Damage Restoration
• Fire & Smoke Damage Restoration
• Remodeling
• Roofing
• New Flooring Sales and Installation
• 24HR Emergency Services
• Commercial Services

Add BOLD, red Call To Action of "CALL NOW" on homepage

Feature image to be around water damage restoration and emergency services (flooded home) – similar to this photo: http://kbsgrv-example.com/images/flood.jpg

Add work and projects section

Keep services icons and descriptions with main focus is Water damage, Fire damage, Storm damage, Roof repair replacement, Exterior repairs and Kitchen/Bath Remodeling

Target Market(s)

Customers looking for home disaster restoration services

Number of Pages Required

2 page

Requirements
Must have
• Responsive Design
• 2 pages submitted - Homepage & Interior page. Designs WILL NOT be considered if 2 pages aren't submitted

```html
<!DOCTYPE html>
<html lang="en">
<head>
<meta charset="utf-8">
<title>Keel Brook Services – Homepage and Services Page</title>
<link href="https://fonts.googleapis.com/css2?family=Poppins:wght@400;500;600;700&family=Open+Sans:wght@400;600&display=swap" rel="stylesheet">
<style>
:root{
  --sky:#31a8f5;
  --navy:#10109a;
  --navy-deep:#0a0a7c;
  --red:#ec1c24;
  --ink:#222233;
  --muted:#6b6b7a;
  --bar:#2a2a2e;
  --light:#efeff2;
  --footer:#e4e4e6;
  --white:#ffffff;
}
*{box-sizing:border-box;margin:0;padding:0}
html,body{width:1200px;height:2510px;overflow:hidden}
body{background:var(--sky);font-family:"Open Sans",Arial,sans-serif;color:var(--ink);position:relative}
h1,h2,h3,h4,.brand,.btn,.nav a{font-family:"Poppins",Arial,sans-serif}
.page{position:absolute;width:540px;background:var(--white);overflow:hidden;box-shadow:0 6px 24px rgba(0,0,40,.25)}
.page-home{left:42px;top:536px}
.page-service{left:626px;top:536px}

/* top bar */
.topbar{height:20px;background:var(--bar);display:flex;align-items:center;justify-content:space-between;padding:0 38px;color:#ddd;font-size:6px}
.topbar .social{display:flex;gap:4px}
.dot-ico{width:9px;height:9px;border-radius:50%;border:1px solid #ccc;display:inline-block}

/* header */
.header{height:57px;display:flex;align-items:center;justify-content:space-between;padding:0 38px}
.brand{display:flex;align-items:center;gap:6px;font-weight:700;font-size:15px;color:var(--navy);line-height:1}
.brand .mark{width:16px;height:16px;background:var(--navy)}
.contact-mini{display:flex;gap:22px;font-size:8px}
.contact-mini b{display:block;font-weight:600;font-size:6.5px;color:var(--ink)}
.contact-mini .phone{color:var(--red);font-weight:700}

/* nav */
.nav{height:32px;background:var(--navy);display:flex;align-items:center;position:relative;padding-left:38px}
.nav a{color:var(--white);text-decoration:none;font-size:6px;font-weight:500;margin-right:9px;white-space:nowrap}
.nav a.active{font-weight:700}
.nav .book{position:absolute;right:0;top:0;height:32px;width:118px;background:var(--red);color:var(--white);display:flex;align-items:center;justify-content:center;font-size:7.5px;font-weight:600;clip-path:polygon(14% 0,100% 0,100% 100%,0 100%);padding-left:12px;white-space:nowrap}

/* hero */
.hero{height:251px;position:relative;background:linear-gradient(160deg,#d9d9d9 0%,#b8b8b6 45%,#6f6f6c 100%)}
.hero-badge{position:absolute;left:54px;top:62px;width:126px;height:126px;border-radius:50%;background:rgba(20,20,24,.88);border:3px solid var(--red);box-shadow:0 0 0 4px rgba(255,255,255,.35);display:flex;flex-direction:column;align-items:center;justify-content:center;text-align:center;color:var(--white)}
.hero-badge h1{font-size:11px;font-weight:600;line-height:1.35}
.hero-badge p{font-size:5.5px;color:#ccc;margin:5px 14px 8px;line-height:1.4}
.btn-red{background:var(--red);color:var(--white);font-size:6.5px;font-weight:600;padding:5px 14px;border-radius:10px}
.slider-dots{position:absolute;right:14px;top:112px;display:flex;flex-direction:column;gap:4px}
.slider-dots i{width:5px;height:5px;border-radius:50%;background:rgba(255,255,255,.6)}
.slider-dots i:first-child{background:var(--white)}

/* welcome */
.welcome{height:288px;position:relative;padding:50px 0 0 40px}
.welcome .eyebrow{font-family:"Poppins",sans-serif;font-size:12px;font-weight:600;color:var(--ink)}
.welcome h2{font-size:14px;font-weight:600;color:var(--navy);margin-top:2px}
.welcome .rule{width:28px;height:2px;background:var(--navy);margin:8px 0 14px}
.welcome p{font-size:6.5px;color:var(--muted);width:220px;line-height:1.7}
.btn-navy{display:inline-block;background:var(--navy);color:var(--white);font-size:7px;font-weight:600;padding:7px 22px;border-radius:12px;margin-top:18px}
.collage{position:absolute;right:28px;top:28px;width:260px;height:220px}
.collage .ph{position:absolute;border:4px solid var(--white);box-shadow:0 3px 10px rgba(0,0,0,.2)}

/* who we are */
.who{height:256px;background:linear-gradient(180deg,#1a1aa6,var(--navy-deep));position:relative;color:var(--white);padding-top:30px}
.section-title{text-align:center;font-size:14px;font-weight:600}
.section-title + .rule{width:26px;height:2px;background:var(--white);margin:6px auto 0}
.features{display:grid;grid-template-columns:1fr 1fr;gap:22px 26px;padding:22px 38px 0}
.feature{display:flex;gap:12px}
.feature .ico{flex:0 0 38px;height:38px;border-radius:50%;background:var(--white);display:flex;align-items:center;justify-content:center}
.feature h3{font-size:8.5px;font-weight:600}
.feature p{font-size:5.8px;line-height:1.6;color:#d4d4f0;margin-top:3px}
.who .more{font-family:"Poppins",sans-serif;font-size:6px;font-weight:600;margin-top:4px;display:block;padding-left:50px}

/* services card */
.services-wrap{position:relative;height:440px;background:linear-gradient(180deg,var(--navy-deep) 0,var(--navy-deep) 48px,var(--white) 48px)}
.services-card{position:absolute;left:42px;top:0;width:456px;height:430px;background:var(--white);box-shadow:0 4px 18px rgba(0,0,0,.18);display:flex;padding:38px 0 0 42px}
.services-left{width:200px}
.services-left h2{font-size:14px;font-weight:600;color:var(--navy);line-height:1.3}
.services-left .rule{width:26px;height:2px;background:var(--navy);margin:8px 0 12px 14px}
.services-left p{font-size:6px;line-height:1.7;color:var(--ink)}
.form-box{margin-top:14px;width:172px;background:var(--navy);padding:14px;color:var(--white)}
.form-box h3{text-align:center;font-size:11px;font-weight:600;margin-bottom:12px}
.field{background:#e9e9ee;height:24px;margin-bottom:4px;font-size:5.5px;color:#888;padding:8px 6px}
.field.tall{height:42px}
.btn-outline{display:inline-block;border:1px solid var(--white);font-size:6.5px;font-weight:600;padding:6px 26px;margin-top:10px}
.services-right{padding-left:48px;padding-top:8px}
.svc{display:flex;align-items:center;gap:12px;height:78px}
.svc .ph{width:64px;height:64px;border-radius:50%}
.svc span{font-family:"Poppins",sans-serif;font-size:8.5px;font-weight:500;color:var(--ink)}
.svc.active span{color:var(--navy);font-weight:600}
.svc.active .ph{box-shadow:0 0 0 3px rgba(16,16,154,.15)}
.card-dots{display:flex;gap:4px;margin:8px 0 0 32px}
.card-dots i{width:5px;height:5px;border-radius:50%;background:#ccc}
.card-dots i:first-child{background:var(--navy)}

/* work */
.work{height:193px;background:linear-gradient(180deg,#1616a0,var(--navy-deep));padding:30px 40px 0;color:var(--white)}
.work-head{display:flex;align-items:center}
.work-head h2{font-size:14px;font-weight:600}
.work-head .tabs{display:flex;gap:10px;font-size:6.5px;margin-left:60px}
.work-head .tabs b{font-weight:700}
.arrows{margin-left:auto;display:flex}
.arrows i{width:20px;height:16px;display:flex;align-items:center;justify-content:center;background:#555;color:var(--white);font-style:normal;font-size:8px}
.arrows i+i{background:var(--white);color:var(--navy)}
.work .rule{width:26px;height:2px;background:var(--white);margin:6px 0 14px 10px}
.projects{display:flex;gap:8px}
.projects .ph{width:148px;height:86px}

/* reviews */
.reviews{height:209px;background:var(--light);position:relative;padding-top:28px}
.reviews h2{text-align:center;font-size:14px;font-weight:600;color:var(--navy)}
.reviews .rule{width:26px;height:2px;background:var(--navy);margin:6px auto 22px}
.review-row{display:flex;gap:14px;justify-content:center}
.review{width:138px;height:92px;background:var(--white);text-align:center;padding:12px 10px 0}
.review p{font-size:5.6px;line-height:1.6;color:var(--ink)}
.review .badge{width:40px;height:12px;background:#d6d6dc;border-radius:3px;margin:8px auto 0}
.side-arrow{position:absolute;top:125px;width:16px;height:16px;background:var(--white);border:1px solid #ccc;font-size:8px;display:flex;align-items:center;justify-content:center;color:#666}

/* footer */
.footer{background:var(--footer);display:grid;grid-template-columns:150px 96px 100px 1fr;padding:18px 24px 0 40px;font-size:6px;color:var(--muted)}
.page-home .footer{height:120px}
.page-service .footer{height:122px}
.footer h4{font-size:8px;font-weight:600;color:var(--ink);margin-bottom:8px}
.footer .brand{font-size:11px;margin-top:14px}
.footer .brand .mark{width:11px;height:11px}
.footer .stay{font-size:7px;color:var(--ink);margin-top:10px;font-weight:600}
.footer .social{display:flex;gap:3px;margin-top:4px;align-items:center}
.footer .social .dot-ico{border-color:#888}
.badges{display:inline-flex;gap:4px;margin-left:8px}
.badges i{width:16px;height:20px;background:var(--navy);opacity:.85}
.footer ul{list-style:none;line-height:2}
.contact-line{display:flex;gap:5px;line-height:1.6;margin-bottom:5px}
.contact-line svg{flex:0 0 7px;margin-top:2px}
.news p{line-height:1.7;margin-bottom:8px}
.news-form{display:flex}
.news-form span{flex:1;background:var(--white);font-size:5px;padding:5px;color:#999}
.news-form i{width:16px;background:var(--navy);color:var(--white);display:flex;align-items:center;justify-content:center;font-style:normal;font-size:8px}
.copyright{background:var(--navy);color:var(--white);font-size:6px;text-align:center;display:flex;align-items:center;justify-content:center}
.page-home .copyright{height:30px}
.page-service .copyright{height:25px}

/* service page */
.banner{height:156px;background:linear-gradient(180deg,#8c8f94,#5b5e63);display:flex;align-items:center;justify-content:center;color:var(--white);font-family:"Poppins",sans-serif;font-size:9px;font-weight:600}
.svc-content{height:447px;position:relative}
.side-nav{position:absolute;left:38px;top:22px;width:128px;list-style:none}
.side-nav li{font-size:6.3px;padding:7px 5px;height:27px;color:var(--ink)}
.side-nav li.active{background:var(--navy);color:var(--white);font-weight:600;height:18px;padding:5px;margin-bottom:6px}
.svc-photo{position:absolute;left:184px;top:20px;width:316px;height:188px}
.support{position:absolute;left:38px;top:230px;width:128px;height:182px;background:linear-gradient(180deg,#2b2bb6,var(--navy-deep));color:var(--white);text-align:center;padding-top:58px}
.support h3{font-size:10px;font-weight:600}
.support p{font-family:"Poppins",sans-serif;font-size:13px;font-weight:600;margin-top:6px;line-height:1.4}
.svc-text{position:absolute;left:184px;top:228px;width:318px}
.svc-text h2{font-size:11px;font-weight:600;color:var(--navy)}
.svc-text p{font-size:5.8px;line-height:1.7;color:var(--muted);margin-top:6px}
.checks{display:grid;grid-template-columns:1fr 1fr;gap:4px 12px;margin-top:10px;list-style:none}
.checks li{font-size:5.8px;display:flex;align-items:center;gap:5px;color:var(--ink)}
.svc-text .btn-navy{margin-top:10px;font-size:6.5px;padding:6px 20px}
</style>
</head>
<body>

<article class="page page-home">
  <div class="topbar">
    <span>New Flooring Sales &amp; Installation &nbsp;|&nbsp; 24HR Emergency Services &nbsp;|&nbsp; Commercial Services</span>
    <span class="social"><i class="dot-ico"></i><i class="dot-ico"></i><i class="dot-ico"></i><i class="dot-ico"></i></span>
  </div>
  <header class="header">
    <div class="brand"><span class="mark"></span>Keel Brook Services</div>
    <div class="contact-mini">
      <div><b>Email</b>info@keelbrook-example.com</div>
      <div><b>Call Now</b><span class="phone">555 010-7184</span></div>
    </div>
  </header>
  <nav class="nav">
    <a class="active">Home</a><a>About Us</a><a>Water Damage Restoration</a><a>Fire &amp; Smoke Damage Restoration</a><a>Remodeling</a><a>Roofing</a>
    <span class="book">Book an Appointment</span>
  </nav>
  <section class="hero" role="img" aria-label="Living room with a white sofa standing in flood water">
    <div class="hero-badge">
      <h1>Professional<br>Cleaning Services</h1>
      <p>Sed ut perspiciatis unde omnis iste natus error sit</p>
      <span class="btn-red">Read More</span>
    </div>
    <div class="slider-dots"><i></i><i></i><i></i></div>
  </section>

  <section class="welcome">
    <div class="eyebrow">Welcome To</div>
    <h2>Pro Carpet Cleaning</h2>
    <div class="rule"></div>
    <p>Keel Brook Services has been serving the Dallas/Ft. Worth area since 1986. Our expertise in a range of services assists us in handling any job that may arise. No job is too large or too small, we make it happen and give you the best quality work at a competitive price.</p>
    <span class="btn-navy">More Info</span>
    <div class="collage">
      <div class="ph" role="img" aria-label="Dark room with warm light" style="left:12px;top:0;width:60px;height:50px;background:linear-gradient(135deg,#2a2a3a,#8a5a3a)"></div>
      <div class="ph" role="img" aria-label="Bright kitchen after restoration" style="left:60px;top:40px;width:120px;height:112px;background:linear-gradient(160deg,#e8e8e4,#a9b4bc)"></div>
      <div class="ph" role="img" aria-label="Technician cleaning a floor" style="left:186px;top:14px;width:62px;height:54px;background:linear-gradient(160deg,#dfe6ea,#8f9ca6)"></div>
      <div class="ph" role="img" aria-label="Water damaged floor" style="left:2px;top:150px;width:52px;height:50px;background:linear-gradient(160deg,#5fb3c9,#2b6f86)"></div>
      <div class="ph" role="img" aria-label="Carpet cleaning machine" style="left:170px;top:156px;width:66px;height:56px;background:linear-gradient(160deg,#c5c8cc,#6e7278)"></div>
    </div>
  </section>

  <section class="who">
    <h2 class="section-title">Who We Are</h2><div class="rule"></div>
    <div class="features">
      <div>
        <div class="feature">
          <span class="ico"><svg width="18" height="18" viewBox="0 0 18 18"><path d="M4 14l8-8M11 3l4 4M3 15h5" stroke="#10109a" stroke-width="1.8" fill="none" stroke-linecap="round"/></svg></span>
          <div><h3>Experience</h3><p>Sed ut perspiciatis unde omnis iste natus error sit voluptatem accusantium doloremque laudantium, totam rem aperiam.</p></div>
        </div>
        <span class="more">Read More &nbsp;→</span>
      </div>
      <div>
        <div class="feature">
          <span class="ico"><svg width="18" height="18" viewBox="0 0 18 18"><rect x="5" y="6" width="8" height="10" rx="2" fill="#10109a"/><path d="M9 6V3h4" stroke="#10109a" stroke-width="1.6" fill="none"/></svg></span>
          <div><h3>Sustainability</h3><p>Sed ut perspiciatis unde omnis iste natus error sit voluptatem accusantium doloremque laudantium, totam rem aperiam.</p></div>
        </div>
        <span class="more">Read More &nbsp;→</span>
      </div>
      <div>
        <div class="feature">
          <span class="ico"><svg width="18" height="18" viewBox="0 0 18 18"><circle cx="9" cy="5" r="2.5" fill="#10109a"/><path d="M5 16v-5a4 4 0 018 0v5z" fill="#10109a"/></svg></span>
          <div><h3>Affordability</h3><p>Sed ut perspiciatis unde omnis iste natus error sit voluptatem accusantium doloremque laudantium, totam rem aperiam.</p></div>
        </div>
        <span class="more">Read More &nbsp;→</span>
      </div>
      <div>
        <div class="feature">
          <span class="ico"><svg width="18" height="18" viewBox="0 0 18 18"><rect x="3" y="7" width="12" height="8" rx="2" fill="#10109a"/><circle cx="9" cy="5" r="2.5" fill="#10109a"/></svg></span>
          <div><h3>Experitise</h3><p>Sed ut perspiciatis unde omnis iste natus error sit voluptatem accusantium doloremque laudantium, totam rem aperiam.</p></div>
        </div>
        <span class="more">Read More &nbsp;→</span>
      </div>
    </div>
  </section>

  <section class="services-wrap">
    <div class="services-card">
      <div class="services-left">
        <h2>Pro Carpet Services<br>We Provide</h2>
        <div class="rule"></div>
        <p>We at Keel Brook know you don't have that kind of time. Call us 24 hours a day for emergencies that disrupt your life.</p>
        <div class="form-box">
          <h3>Get In Touch</h3>
          <div class="field">Name</div>
          <div class="field">Email</div>
          <div class="field">Phone Number</div>
          <div class="field tall">Message</div>
          <span class="btn-outline">SUBMIT</span>
        </div>
      </div>
      <div class="services-right">
        <div class="svc"><span class="ph" role="img" aria-label="Flooded room" style="background:linear-gradient(160deg,#c9ccd0,#6d7075)"></span><span>Water Damage</span></div>
        <div class="svc active"><span class="ph" role="img" aria-label="Fire damaged house" style="background:linear-gradient(160deg,#3a3a3a,#111)"></span><span>Fire Damage</span></div>
        <div class="svc"><span class="ph" role="img" aria-label="Storm surge over a coastline" style="background:linear-gradient(160deg,#7fc2e8,#2c6f9e)"></span><span>Storm Damage</span></div>
        <div class="svc"><span class="ph" role="img" aria-label="Worker repairing an exterior wall" style="background:linear-gradient(160deg,#d8b08a,#7a4b30)"></span><span>Exterior Repairs</span></div>
        <div class="card-dots"><i></i><i></i></div>
      </div>
    </div>
  </section>

  <section class="work">
    <div class="work-head">
      <h2>Work &amp; Projects</h2>
      <div class="tabs"><b>All</b><span>Water Damage</span><span>Fire Damage</span><span>Storm Damage</span></div>
      <div class="arrows"><i>‹</i><i>›</i></div>
    </div>
    <div class="rule"></div>
    <div class="projects">
      <div class="ph" role="img" aria-label="Workers repairing a floor" style="background:linear-gradient(160deg,#a7826a,#4a3426)"></div>
      <div class="ph" role="img" aria-label="Firefighter spraying water on a fire" style="background:linear-gradient(160deg,#e08a3a,#7a2a10)"></div>
      <div class="ph" role="img" aria-label="Crew clearing storm debris" style="background:linear-gradient(160deg,#8fa6bd,#3d4d5c)"></div>
    </div>
  </section>

  <section class="reviews">
    <h2>Client Reviews</h2><div class="rule"></div>
    <div class="review-row">
      <div class="review"><p>Lorem ipsum dolor sit amet, consectetur adipiscing elit, sed do eiusmod tempor incididunt ut labore et dolore magna aliqua.</p><div class="badge"></div></div>
      <div class="review"><p>Lorem ipsum dolor sit amet, consectetur adipiscing elit, sed do eiusmod tempor incididunt ut labore et dolore magna aliqua.</p><div class="badge"></div></div>
      <div class="review"><p>Lorem ipsum dolor sit amet, consectetur adipiscing elit, sed do eiusmod tempor incididunt ut labore et dolore magna aliqua.</p><div class="badge"></div></div>
    </div>
    <span class="side-arrow" style="left:4px">‹</span>
    <span class="side-arrow" style="right:4px">›</span>
  </section>

  <footer class="footer">
    <div>
      <div class="brand"><span class="mark"></span>Keel Brook Services</div>
      <div class="stay">Stay Connected</div>
      <div class="social"><i class="dot-ico"></i><i class="dot-ico"></i><i class="dot-ico"></i><i class="dot-ico"></i><span class="badges"><i></i><i></i></span></div>
    </div>
    <div><h4>Links</h4><ul><li>Home</li><li>About Us</li><li>Services</li><li>Work &amp; Projects</li><li>Contact Us</li></ul></div>
    <div>
      <h4>Contact Us</h4>
      <div class="contact-line"><svg width="7" height="8" viewBox="0 0 7 8"><path d="M3.5 0a3 3 0 013 3c0 2-3 5-3 5S.5 5 .5 3a3 3 0 013-3z" fill="#333"/></svg><span>416, 123 Street,<br>Location, USA</span></div>
      <div class="contact-line"><svg width="7" height="7" viewBox="0 0 7 7"><path d="M1 0h2l1 2-1 1a4 4 0 002 2l1-1 1 1v2C3 7 0 4 0 1z" fill="#333"/></svg><span>555 010-7184<br>555 010-1042</span></div>
      <div class="contact-line"><svg width="7" height="6" viewBox="0 0 7 6"><rect width="7" height="6" fill="#333"/><path d="M0 0l3.5 3L7 0" stroke="#fff" fill="none" stroke-width=".8"/></svg><span>info@keelbrook-example.com</span></div>
    </div>
    <div class="news">
      <h4>Newsletter</h4>
      <p>But I must explain to you how all this mistaken idea of denouncing pleasure and praising.</p>
      <div class="news-form"><span>Enter your email address</span><i>→</i></div>
    </div>
  </footer>
  <div class="copyright">© 2018 Copyrights | All Rights Reserved</div>
</article>

<article class="page page-service">
  <div class="topbar">
    <span>New Flooring Sales &amp; Installation &nbsp;|&nbsp; 24HR Emergency Services &nbsp;|&nbsp; Commercial Services</span>
    <span class="social"><i class="dot-ico"></i><i class="dot-ico"></i><i class="dot-ico"></i><i class="dot-ico"></i></span>
  </div>
  <header class="header">
    <div class="brand"><span class="mark"></span>Keel Brook Services</div>
    <div class="contact-mini">
      <div><b>Email</b>info@keelbrook-example.com</div>
      <div><b>Call Now</b><span class="phone">555 010-7184</span></div>
    </div>
  </header>
  <nav class="nav">
    <a class="active">Home</a><a>About Us</a><a>Water Damage Restoration</a><a>Fire &amp; Smoke Damage Restoration</a><a>Remodeling</a><a>Roofing</a>
    <span class="book">Book an Appointment</span>
  </nav>
  <section class="banner" role="img" aria-label="Cleaning crew working in an office stairwell">Home &nbsp;&gt;&nbsp; Services</section>

  <section class="svc-content">
    <ul class="side-nav">
      <li class="active">Pro Carpet Cleaning</li>
      <li>Fire &amp; Smoke Damage</li>
      <li>Air Duct Cleaning</li>
      <li>Emergency Flood Services</li>
      <li>Upholstery Cleaning</li>
      <li>New Flooring Sales &amp; Installation</li>
      <li>Commercial Services</li>
    </ul>
    <div class="svc-photo" role="img" aria-label="Technician steam cleaning an office floor" style="background:linear-gradient(160deg,#e6ecef,#9fb0b8)"></div>
    <div class="support" role="img" aria-label="Support agent with headset on a blue background">
      <h3>Online Support</h3>
      <p>555 010-7184<br>555 010-1042</p>
    </div>
    <div class="svc-text">
      <h2>Pro Carpet Cleaning</h2>
      <p>From carpets to air ducts, Keel Brook Services provides superior cleaning services for your home or business. We offer many services, including:</p>
      <ul class="checks">
        <li><svg width="8" height="8" viewBox="0 0 8 8"><path d="M1 4l2 2 4-5" stroke="#10109a" stroke-width="1.2" fill="none"/></svg>24 Hour / 7 Days Flood Emergency Service</li>
        <li><svg width="8" height="8" viewBox="0 0 8 8"><path d="M1 4l2 2 4-5" stroke="#10109a" stroke-width="1.2" fill="none"/></svg>Oriental Rugs</li>
        <li><svg width="8" height="8" viewBox="0 0 8 8"><path d="M1 4l2 2 4-5" stroke="#10109a" stroke-width="1.2" fill="none"/></svg>Truck Mounted Equipment</li>
        <li><svg width="8" height="8" viewBox="0 0 8 8"><path d="M1 4l2 2 4-5" stroke="#10109a" stroke-width="1.2" fill="none"/></svg>Carpet Repairs and Restretching</li>
        <li><svg width="8" height="8" viewBox="0 0 8 8"><path d="M1 4l2 2 4-5" stroke="#10109a" stroke-width="1.2" fill="none"/></svg>Carpet Steam Cleaning</li>
        <li><svg width="8" height="8" viewBox="0 0 8 8"><path d="M1 4l2 2 4-5" stroke="#10109a" stroke-width="1.2" fill="none"/></svg>Pet Odor Removal Specialist</li>
        <li><svg width="8" height="8" viewBox="0 0 8 8"><path d="M1 4l2 2 4-5" stroke="#10109a" stroke-width="1.2" fill="none"/></svg>Upholstery Cleaning</li>
        <li><svg width="8" height="8" viewBox="0 0 8 8"><path d="M1 4l2 2 4-5" stroke="#10109a" stroke-width="1.2" fill="none"/></svg>Air Duct Cleaning Specialist</li>
        <li></li>
        <li><svg width="8" height="8" viewBox="0 0 8 8"><path d="M1 4l2 2 4-5" stroke="#10109a" stroke-width="1.2" fill="none"/></svg>New Carpet Sales and Installation</li>
      </ul>
      <p>The condition of your carpet is of utmost importance to you, and the technicians at Keel Brook Services are trained to provide your carpet with the care it deserves. Keel Brook technicians will move most furniture, pre-vacuum, and apply a stain pretreatment to your carpet.</p>
      <span class="btn-navy">More Info</span>
    </div>
  </section>

  <footer class="footer">
    <div>
      <div class="brand"><span class="mark"></span>Keel Brook Services</div>
      <div class="stay">Stay Connected</div>
      <div class="social"><i class="dot-ico"></i><i class="dot-ico"></i><i class="dot-ico"></i><i class="dot-ico"></i><span class="badges"><i></i><i></i></span></div>
    </div>
    <div><h4>Links</h4><ul><li>Home</li><li>About Us</li><li>Services</li><li>Work &amp; Projects</li><li>Contact Us</li></ul></div>
    <div>
      <h4>Contact Us</h4>
      <div class="contact-line"><svg width="7" height="8" viewBox="0 0 7 8"><path d="M3.5 0a3 3 0 013 3c0 2-3 5-3 5S.5 5 .5 3a3 3 0 013-3z" fill="#333"/></svg><span>416, 123 Street,<br>Location, USA</span></div>
      <div class="contact-line"><svg width="7" height="7" viewBox="0 0 7 7"><path d="M1 0h2l1 2-1 1a4 4 0 002 2l1-1 1 1v2C3 7 0 4 0 1z" fill="#333"/></svg><span>555 010-7184<br>555 010-1042</span></div>
      <div class="contact-line"><svg width="7" height="6" viewBox="0 0 7 6"><rect width="7" height="6" fill="#333"/><path d="M0 0l3.5 3L7 0" stroke="#fff" fill="none" stroke-width=".8"/></svg><span>info@keelbrook-example.com</span></div>
    </div>
    <div class="news">
      <h4>Newsletter</h4>
      <p>But I must explain to you how all this mistaken idea of denouncing pleasure and praising.</p>
      <div class="news-form"><span>Enter your email address</span><i>→</i></div>
    </div>
  </footer>
  <div class="copyright">© 2018 Copyrights | All Rights Reserved</div>
</article>

</body>
</html>
```